New Wrestling company needs a website

We need a website design for a new wrestling company in Australia that will be running 3-4 events per year. Wrestling company is Summit Grip Wrestling (SGW).

The design of the logo is in place and can be provided, and I have purchased the website domain.

A detailed description of the intent and purpose of this company can be provided.

The aim would be to have around 5 specific pages on SGW, with two standard “about” and “contact” pages. E.g.
- About SGW (focus and purpose of the company)
- SGW Events (specific focus on events run by SGW)
- SGW News (news and stories on wrestling’s across Oceania)
- SGW Media (where to watch SGW and our partners))
- SGW Partners and Sponsors (partner and affiliate information)
- SGW Power Rankings (top 10 ranked wrestlers from Oceania which is updated weekly)
- SGW fans (highlighting how to become part of SGW as a fan)
- Contact SGW
Updates

The logo design should now be included in the brief, please feel free to reach out to me directly if you can't access it or require any other information.

Target Market(s)

Wrestling Fans

Industry/Entity Type

Sport / Wrestling

Coding

Coded - Design and coding required

Number of Pages Required

5+ page

Requirements
Must have
• A Wrestling and or Sports feel to the website design

```html
<!DOCTYPE html>
<html lang="en">
<head>
<meta charset="utf-8">
<title>Summit Grip Wrestling</title>
<link href="https://fonts.googleapis.com/css2?family=Poppins:wght@400;500;600;700;800&family=Lato:wght@400;700&display=swap" rel="stylesheet">
<style>
:root{
  --blue:#2a7fc9;
  --blue-dark:#1f6cb0;
  --navy:#1d3d72;
  --ink:#1e1e1e;
  --text:#555;
  --white:#fff;
  --black:#050505;
  --line:#dde3ea;
}
*{margin:0;padding:0;box-sizing:border-box}
html,body{width:1200px;height:4608px;overflow:hidden}
body{font-family:"Lato",sans-serif;color:var(--ink);background:var(--white);position:relative}
h1,h2,h3,.heading{font-family:"Poppins",sans-serif}
section,header,footer,nav{position:relative;width:1200px}
.btn{display:inline-block;font-family:"Poppins",sans-serif;font-weight:600;font-size:14px;text-transform:uppercase;border-radius:20px;padding:9px 21px;letter-spacing:.2px}
.btn-blue{background:var(--blue);color:var(--white)}
.btn-white{background:var(--white);color:var(--blue)}

/* header */
.topbar{height:80px}
.brand{position:absolute;left:112px;top:14px;display:flex;align-items:center;gap:10px}
.brand-mark{width:46px;height:46px;border-radius:50%;background:var(--blue)}
.brand-name{font-family:"Poppins",sans-serif;font-weight:700;font-size:30px;color:var(--blue)}
.contact-chip{position:absolute;top:22px;display:flex;align-items:center;gap:14px}
.chip-icon{width:40px;height:40px;border-radius:50%;background:var(--blue);display:flex;align-items:center;justify-content:center}
.chip-label{font-family:"Poppins",sans-serif;font-size:13px;font-weight:500;text-transform:uppercase}
.chip-value{font-size:12.5px;margin-top:2px}
.login{position:absolute;left:982px;top:22px;width:104px;text-align:center;padding:9px 0}
.mainnav{height:60px;background:var(--blue);display:flex;justify-content:center;align-items:center;gap:44px}
.mainnav a{color:var(--white);font-family:"Poppins",sans-serif;font-weight:500;font-size:14.5px;text-transform:uppercase;text-decoration:none}

/* hero */
.hero{height:600px;overflow:hidden}
.hero-photo{position:absolute;inset:0;background:linear-gradient(90deg,#10182a 0%,#1e2838 40%,#5a3e30 70%,#2a1c18 100%)}
.hero-copy{position:absolute;left:112px;top:150px;width:480px;color:var(--white)}
.hero-copy h1{font-size:66px;font-weight:800;line-height:1.16;text-transform:uppercase}
.hero-copy p{font-size:15px;line-height:1.7;margin:12px 0 24px}
.arrow{position:absolute;width:52px;height:52px;border-radius:50%;display:flex;align-items:center;justify-content:center}
.hero .arrow{top:274px}
.arrow-light{background:var(--white)}
.arrow-blue{background:var(--blue)}

/* about */
.about{height:590px}
.about-photo{position:absolute;left:113px;top:57px;width:418px;height:418px;border-radius:50%;border:12px solid var(--blue);background:radial-gradient(circle at 50% 45%,#4a5a7a,#1b2030 70%)}
.about-copy{position:absolute;left:599px;top:86px;width:488px}
.eyebrow{font-family:"Poppins",sans-serif;font-size:13px;font-weight:600;color:var(--blue);text-transform:uppercase}
.about-copy h2{font-size:30px;font-weight:500;line-height:1.38;margin:8px 0 18px}
.about-copy p{font-size:14.5px;line-height:1.78;color:var(--text);text-align:justify;margin-bottom:24px}

/* media */
.media{height:513px;background:var(--blue);color:var(--white)}
.media-copy{position:absolute;left:112px;top:70px;width:422px}
.media-copy h2{font-size:29px;font-weight:500;text-transform:uppercase}
.media-copy .sub{font-size:14px;margin:6px 0 30px}
.media-copy p{font-size:14px;line-height:1.82;text-align:justify;margin-bottom:38px}
.media-video{position:absolute;left:600px;top:0;width:600px;height:513px;background:linear-gradient(180deg,#2c2c2c 0%,#1a1a1a 55%,#1c2550 100%)}
.play{position:absolute;left:268px;top:222px;width:66px;height:66px;border-radius:50%;background:var(--white);display:flex;align-items:center;justify-content:center}

/* news */
.news{height:729px;text-align:center}
.section-title{font-size:29px;font-weight:500;text-transform:uppercase}
.section-sub{font-size:14px;margin-top:10px;color:#333}
.news .section-title{padding-top:80px}
.cards{position:absolute;left:111px;top:189px;display:flex;gap:23px;text-align:left}
.card{width:311px;height:454px;background:var(--white);box-shadow:0 2px 10px rgba(0,0,0,.16);border-bottom:3px solid var(--navy)}
.card-photo{height:214px}
.card-body{padding:24px 24px 0}
.card-date{display:flex;align-items:center;gap:8px;font-family:"Poppins",sans-serif;font-size:15px;color:var(--navy);font-weight:500}
.card h3{font-size:19px;font-weight:400;line-height:1.38;margin:18px 0 14px}
.card p{font-size:14px;line-height:1.8;color:#444}
.card a{display:inline-block;margin-top:12px;font-family:"Poppins",sans-serif;font-size:14.5px;font-weight:600;color:var(--navy)}

/* ranking */
.ranking{height:686px;overflow:hidden;color:var(--white)}
.ranking-bg{position:absolute;inset:0;background:radial-gradient(ellipse at 40% 20%,#3c68a8 0%,#1b3566 55%,#0e1c3a 100%)}
.ranking-head{position:absolute;left:111px;top:58px}
.ranking-head h2{font-size:32px;font-weight:600;text-transform:uppercase}
.ranking-head p{font-size:14px;margin-top:10px}
.rank-table{position:absolute;left:111px;top:175px;width:619px;border-collapse:collapse;background:var(--blue);font-family:"Poppins",sans-serif}
.rank-table th{height:80px;font-size:24px;font-weight:500}
.rank-table td{height:36.2px;font-size:16px;text-transform:uppercase;text-align:center;border-top:1px solid rgba(255,255,255,.25)}
.rank-table .col-rank{width:190px;text-align:left;padding-left:60px}
.rank-table th.col-rank{padding-left:60px}
.rank-table .col-rate{width:150px}
.rank-table td.col-rank{padding-left:62px}
.rank-table tr.lead td{background:var(--white);color:var(--blue)}
.athlete{position:absolute;left:750px;top:110px;width:450px;height:576px;background:linear-gradient(180deg,rgba(170,110,70,.55),rgba(90,55,35,.8) 70%,rgba(20,20,25,.9))}

/* partners */
.partners{height:475px;text-align:center}
.partners .section-title{padding-top:82px}
.logo-badge{position:absolute;width:170px;height:170px;border-radius:50%;background:var(--white);box-shadow:0 3px 12px rgba(0,0,0,.18);display:flex;align-items:center;justify-content:center}
.logo-badge span{width:96px;height:70px;border-radius:10px;background:#d4d8de}
.partners .arrow{top:223px;width:40px;height:40px}
.arrow-outline{background:var(--white);box-shadow:0 1px 6px rgba(0,0,0,.2)}

/* contact */
.contact{height:540px;background:var(--blue-dark);color:var(--white)}
.contact-map{position:absolute;inset:0;background:linear-gradient(135deg,#2d7fc7,#2570b5 60%,#2a78bf)}
.contact-info{position:absolute;left:111px;top:68px}
.contact-info h2{font-size:30px;font-weight:600;text-transform:uppercase;margin-bottom:34px}
.info-row{display:flex;gap:24px;margin-bottom:26px}
.info-icon{width:46px;height:46px;border-radius:50%;background:var(--white);display:flex;align-items:center;justify-content:center;flex-shrink:0;margin-top:12px}
.info-row h3{font-size:19px;font-weight:500}
.info-row p{font-size:14.5px;line-height:1.7;margin-top:4px}
.form-box{position:absolute;left:545px;top:68px;width:542px;height:404px;background:var(--white);padding:34px 28px;color:var(--ink)}
.form-box h3{font-size:29px;font-weight:500;text-align:center;margin-bottom:24px}
.field-row{display:flex;gap:6px;margin-bottom:14px}
.field{flex:1;height:47px;border:1px solid var(--line);font-size:13px;color:#777;padding:14px 12px}
.field.msg{height:92px}
.submit{display:block;width:140px;margin:4px auto 0;text-align:center;padding:9px 0}

/* footer */
.site-footer{height:335px;background:var(--black);color:var(--white);text-align:center}
.foot-brand{position:absolute;left:0;right:0;top:80px;display:flex;justify-content:center;align-items:center;gap:10px}
.foot-brand .brand-mark{width:38px;height:38px}
.foot-nav{position:absolute;top:155px;left:0;right:0;display:flex;justify-content:center;gap:30px}
.foot-nav a{color:var(--white);text-decoration:none;font-size:15px}
.copyright{position:absolute;top:206px;left:0;right:0;font-size:15px}
.socials{position:absolute;top:260px;left:0;right:0;display:flex;justify-content:center;gap:20px}
.socials span{width:15px;height:15px;border-radius:50%;background:var(--white)}
</style>
</head>
<body>

<header class="topbar">
  <div class="brand"><span class="brand-mark"></span><span class="brand-name">SGW</span></div>
  <div class="contact-chip" style="left:513px">
    <span class="chip-icon"><svg width="16" height="12" viewBox="0 0 16 12"><rect x="0.5" y="0.5" width="15" height="11" rx="1" fill="#fff"/><path d="M1 1l7 6 7-6" stroke="#2a7fc9" stroke-width="1.5" fill="none"/></svg></span>
    <div><div class="chip-label">Email</div><div class="chip-value">info@summitgripwrestling.com</div></div>
  </div>
  <div class="contact-chip" style="left:778px">
    <span class="chip-icon"><svg width="16" height="16" viewBox="0 0 24 24"><path d="M6.6 10.8a15 15 0 006.6 6.6l2.2-2.2a1 1 0 011-.25 11.4 11.4 0 003.6.57 1 1 0 011 1V20a1 1 0 01-1 1A17 17 0 013 4a1 1 0 011-1h3.5a1 1 0 011 1c0 1.25.2 2.45.57 3.57a1 1 0 01-.25 1z" fill="#fff"/></svg></span>
    <div><div class="chip-label">Phone</div><div class="chip-value">+61 (02) 5550 1427</div></div>
  </div>
  <a class="btn btn-blue login">Log In</a>
</header>

<nav class="mainnav">
  <a>Home</a><a>About</a><a>Event</a><a>News</a><a>Media</a><a>Partners</a><a>Power Ranking</a><a>Fans</a><a>Contact</a>
</nav>

<section class="hero">
  <div class="hero-photo" role="img" aria-label="Boxer in red gloves in front of a harbour city skyline at dusk"></div>
  <div class="hero-copy">
    <h1>Summit Grip Wrestling</h1>
    <p>Lorem ipsum dolor sit amet, consectetur adipiscing elit, sed do eiusmod tempor incididunt ut labore et dolore magna aliqua.</p>
    <a class="btn btn-blue">Get Started</a>
  </div>
  <span class="arrow arrow-light" style="left:42px"><svg width="14" height="14" viewBox="0 0 14 14"><path d="M9 2L4 7l5 5" stroke="#2a7fc9" stroke-width="2" fill="none"/></svg></span>
  <span class="arrow arrow-blue" style="left:1098px"><svg width="14" height="14" viewBox="0 0 14 14"><path d="M5 2l5 5-5 5" stroke="#fff" stroke-width="2" fill="none"/></svg></span>
</section>

<section class="about">
  <div class="about-photo" role="img" aria-label="Two wrestlers grappling mid-takedown"></div>
  <div class="about-copy">
    <div class="eyebrow">About Us</div>
    <h2>Focus and Purpose of the Company</h2>
    <p>Lorem ipsum dolor sit amet, consectetur adipiscing elit, sed do eiusmod tempor incididunt ut labore et dolore magna aliqua. Ut enim ad minim veniam, quis nostrud exercitation ullamco laboris nisi ut aliquip ex ea commodo consequat. Duis aute irure dolor in reprehenderit in voluptate velit esse cillum dolore eu fugiat nulla pariatur. Excepteur sint occaecat cupidatat non proident, sunt in culpa qui officia deserunt mollit anim id est laborum.</p>
    <a class="btn btn-blue">Learn More</a>
  </div>
</section>

<section class="media">
  <div class="media-copy">
    <h2>SGW Media</h2>
    <div class="sub">Where to watch SGW and our partners</div>
    <p>Lorem ipsum dolor sit amet, consectetur adipiscing elit, sed do eiusmod tempor incididunt ut labore et dolore magna aliqua. Ut enim ad minim veniam, quis nostrud exercitation ullamco laboris nisi ut aliquip ex ea commodo consequat. Duis aute irure dolor in reprehenderit in voluptate velit esse cillum dolore eu fugiat nulla pariatur. Excepteur sint occaecat cupidatat non proident, sunt in culpa qui officia deserunt mollit anim id est laborum.</p>
    <a class="btn btn-white">Watch Video</a>
  </div>
  <div class="media-video" role="img" aria-label="Video still of wrestlers throwing in a dark gym">
    <span class="play"><svg width="20" height="22" viewBox="0 0 20 22"><path d="M3 2l15 9-15 9z" fill="#2a7fc9"/></svg></span>
  </div>
</section>

<section class="news">
  <h2 class="section-title">Latest From The News</h2>
  <p class="section-sub">News and stories on wrestling's across Oceania</p>
  <div class="cards">
    <article class="card">
      <div class="card-photo" role="img" aria-label="Freestyle wrestlers under arena lights" style="background:linear-gradient(160deg,#3a3f4a,#101216)"></div>
      <div class="card-body">
        <div class="card-date"><svg width="18" height="18" viewBox="0 0 18 18"><circle cx="9" cy="9" r="7.5" stroke="#1d3d72" stroke-width="2" fill="none"/><path d="M9 5v4l3 2" stroke="#1d3d72" stroke-width="2" fill="none"/></svg>Jan 11,2022</div>
        <h3>Sed ut perspiciatis unde omnis iste natus error sit</h3>
        <p>Lorem ipsum dolor sit amet, consectetur adipiscing elit, sed do</p>
        <a>Learn More</a>
      </div>
    </article>
    <article class="card">
      <div class="card-photo" role="img" aria-label="Wrestlers on a blue mat in a pin hold" style="background:linear-gradient(160deg,#3b6fb0,#c8455a 70%,#e8e0d8)"></div>
      <div class="card-body">
        <div class="card-date"><svg width="18" height="18" viewBox="0 0 18 18"><circle cx="9" cy="9" r="7.5" stroke="#1d3d72" stroke-width="2" fill="none"/><path d="M9 5v4l3 2" stroke="#1d3d72" stroke-width="2" fill="none"/></svg>Jan 11,2022</div>
        <h3>Sed ut perspiciatis unde omnis iste natus error sit</h3>
        <p>Lorem ipsum dolor sit amet, consectetur adipiscing elit, sed do</p>
        <a>Learn More</a>
      </div>
    </article>
    <article class="card">
      <div class="card-photo" role="img" aria-label="Pro wrestlers clashing inside a ring" style="background:linear-gradient(160deg,#1a2030,#5a3a30 60%,#20242e)"></div>
      <div class="card-body">
        <div class="card-date"><svg width="18" height="18" viewBox="0 0 18 18"><circle cx="9" cy="9" r="7.5" stroke="#1d3d72" stroke-width="2" fill="none"/><path d="M9 5v4l3 2" stroke="#1d3d72" stroke-width="2" fill="none"/></svg>Jan 11,2022</div>
        <h3>Sed ut perspiciatis unde omnis iste natus error sit</h3>
        <p>Lorem ipsum dolor sit amet, consectetur adipiscing elit, sed do</p>
        <a>Learn More</a>
      </div>
    </article>
  </div>
</section>

<section class="ranking">
  <div class="ranking-bg" role="img" aria-label="Empty wrestling ring under blue arena lights"></div>
  <div class="ranking-head">
    <h2>SGW Power Ranking</h2>
    <p>New wrestling company in Australia that will be running 3-4 events per year</p>
  </div>
  <table class="rank-table">
    <thead><tr><th class="col-rank">RANK</th><th>PLAYER</th><th class="col-rate">RATING</th></tr></thead>
    <tbody>
      <tr class="lead"><td class="col-rank">1</td><td>Jace Tarrant</td><td class="col-rate">09</td></tr>
      <tr><td class="col-rank">2</td><td>Mako Reyes</td><td class="col-rate">07</td></tr>
      <tr><td class="col-rank">3</td><td>Dane Kowalik</td><td class="col-rate">06</td></tr>
      <tr><td class="col-rank">4</td><td>Rhys Callaway</td><td class="col-rate">06</td></tr>
      <tr><td class="col-rank">5</td><td>Tane Whitlock</td><td class="col-rate">05</td></tr>
      <tr><td class="col-rank">6</td><td>Boris Antanov</td><td class="col-rate">05</td></tr>
      <tr><td class="col-rank">7</td><td>Niko Varela</td><td class="col-rate">04</td></tr>
      <tr><td class="col-rank">8</td><td>Luka Pemberton</td><td class="col-rate">04</td></tr>
      <tr><td class="col-rank">9</td><td>Otis Marlowe</td><td class="col-rate">04</td></tr>
      <tr><td class="col-rank">10</td><td>Kai Moreno</td><td class="col-rate">03</td></tr>
    </tbody>
  </table>
  <div class="athlete" role="img" aria-label="Muscular shirtless wrestler standing in the ring"></div>
</section>

<section class="partners">
  <h2 class="section-title">SGW Partners And Sponsors</h2>
  <span class="arrow arrow-blue" style="left:53px"><svg width="14" height="14" viewBox="0 0 14 14"><path d="M12 7H2M6 3L2 7l4 4" stroke="#fff" stroke-width="1.8" fill="none"/></svg></span>
  <div class="logo-badge" style="left:113px;top:164px"><span></span></div>
  <div class="logo-badge" style="left:315px;top:207px"><span></span></div>
  <div class="logo-badge" style="left:516px;top:164px"><span></span></div>
  <div class="logo-badge" style="left:716px;top:207px"><span></span></div>
  <div class="logo-badge" style="left:918px;top:164px"><span></span></div>
  <span class="arrow arrow-outline" style="left:1103px"><svg width="14" height="14" viewBox="0 0 14 14"><path d="M2 7h10M8 3l4 4-4 4" stroke="#555" stroke-width="1.6" fill="none"/></svg></span>
</section>

<section class="contact">
  <div class="contact-map" role="img" aria-label="Faint map of Australia and Oceania"></div>
  <div class="contact-info">
    <h2>Contact Us</h2>
    <div class="info-row">
      <span class="info-icon"><svg width="16" height="20" viewBox="0 0 16 20"><path d="M8 0a8 8 0 00-8 8c0 6 8 12 8 12s8-6 8-12a8 8 0 00-8-8z" fill="#2a7fc9"/><circle cx="8" cy="8" r="3" fill="#fff"/></svg></span>
      <div><h3>Address</h3><p>Lorem ipsum dolor sit amet,<br>consectetur adipiscing</p></div>
    </div>
    <div class="info-row">
      <span class="info-icon"><svg width="18" height="18" viewBox="0 0 24 24"><path d="M6.6 10.8a15 15 0 006.6 6.6l2.2-2.2a1 1 0 011-.25 11.4 11.4 0 003.6.57 1 1 0 011 1V20a1 1 0 01-1 1A17 17 0 013 4a1 1 0 011-1h3.5a1 1 0 011 1c0 1.25.2 2.45.57 3.57a1 1 0 01-.25 1z" fill="#2a7fc9"/></svg></span>
      <div><h3>Phone</h3><p>+61 (02) 5550 1427</p></div>
    </div>
    <div class="info-row">
      <span class="info-icon"><svg width="18" height="14" viewBox="0 0 16 12"><rect x="0.5" y="0.5" width="15" height="11" rx="1" fill="#2a7fc9"/><path d="M1 1l7 6 7-6" stroke="#fff" stroke-width="1.4" fill="none"/></svg></span>
      <div><h3>Email</h3><p>hello@summitgripwrestling.com</p></div>
    </div>
  </div>
  <div class="form-box">
    <h3>Get In Touch</h3>
    <div class="field-row"><div class="field">First name</div><div class="field">Last name</div></div>
    <div class="field-row"><div class="field">Phone</div><div class="field">Email</div></div>
    <div class="field-row"><div class="field msg">Message</div></div>
    <a class="btn btn-blue submit">Submit Now</a>
  </div>
</section>

<footer class="site-footer">
  <div class="foot-brand"><span class="brand-mark"></span><span class="brand-name">SGW</span></div>
  <div class="foot-nav">
    <a>Home</a><a>About</a><a>Event</a><a>News</a><a>Media</a><a>Partners</a><a>Power Ranking</a><a>Fans</a><a>Contact</a>
  </div>
  <p class="copyright">©Copyrights 2022 Summit Grip Wrestling &nbsp;| &nbsp; All Rights Reserved</p>
  <div class="socials"><span></span><span></span><span></span><span></span><span></span></div>
</footer>

</body>
</html>
```